Plenko - Shoe Fitting App : Foot scanning app, 3D reconstruction and Fit recommandation.

We are a startup that has developed a 3D scanning App that compares the 3d reconstructed foot to the 3D Last (mould) of a shoe to find the best match and recommend a shoe size with a graphical representation of the fit on a reconstructed foot without texturing. The challenge of this app is to have a simple and intuitive onboarding of the user with clean and crisp ui and a simple tutorial for foot scanning. 3D representation of the fit is also key. What you see is what you feel is what we would like to achieve.

Target Market(s)

Sneaker Brands and athletic shoes brands

Industry/Entity Type

Footwear

Font styles to use
Other font styles liked:
• Oswald or Droid Serif

Colors
0094D4
00A9DD
6FCCEA
C7EBF8
E9F6FB

Requirements
Must have
• Simple intuitive UI to onboard the customer to scan his bare foot (please look at attached image on how to scan the foot). You must flip your phone so that the screen is facing your foot. Start at 40cm distance form the front of your foot and turn 360% slowly to capture the foot while you feel the aptic of the Phone. That needs to be presented with a simple animation that the user can easily understand and skip if he is a returning customer and knows how to do that. the rest of the UI is to present the result of the scanned foot for the user to use to get his fit and size. The other must have is the final result screen. Where the user will a representation of the foot (snug, loose ) of different predefined areas of the foot so he can choose the fit that he likes and not necessarily the size that we suggest. Must match website design (https://www.plenko.example)
Nice to have
• An animation of the whole process (scan-compare 3d foot with 3d shoe last(or mould) and get the 3D result of the best fit + associated size. Optionaly, an option to play with your foot and transform it (avatar like with accessories and colours)
Should not have
• Too many colours. Too much text. No gender type. No race type.

```html
<!DOCTYPE html>
<html lang="en">
<head>
<meta charset="utf-8">
<title>Plenko – Onboarding</title>
<link rel="stylesheet" href="https://fonts.googleapis.com/css2?family=Poppins:wght@700&family=Noto+Serif:wght@400&family=Inter:wght@400;500;600&display=swap">
<style>
  :root{
    --stage:#1e1e1e;
    --splash:#171717;
    --card:#ffffff;
    --ink:#2b2b2b;
    --muted:#8a8a8a;
    --teal:#4db6b6;
    --teal-soft:#d8f1f1;
    --dash:#3a3d3f;
    --button:#3a3d3f;
    --home:#1f4a43;
    --white:#ffffff;
  }
  *{box-sizing:border-box;margin:0;padding:0}
  html,body{width:1200px;height:491px;overflow:hidden;background:var(--stage)}
  .board{position:relative;width:1200px;height:491px;background:var(--stage)}
  .board-title{
    position:absolute;left:0;right:0;top:34px;text-align:center;
    font-family:"Poppins",sans-serif;font-weight:700;font-size:68px;line-height:80px;
    color:var(--white);letter-spacing:-1px;
  }
  .screens{position:absolute;left:65px;top:164px;display:flex;gap:13.8px}
  .screen{position:relative;width:106.6px;height:231px;border-radius:6.5px;background:var(--card);overflow:hidden}
  .screen--splash{background:var(--splash);display:flex;align-items:center;justify-content:center}
  .brand-name{font-family:"Poppins",sans-serif;font-weight:700;font-size:19px;color:var(--white);letter-spacing:.5px;margin-top:8px}
  .status-bar{position:absolute;top:5px;left:8px;right:6px;height:6px;display:flex;justify-content:space-between;align-items:center;
    font-family:"Inter",sans-serif;font-weight:600;font-size:4.4px;color:var(--ink)}
  .status-icons{display:flex;gap:1.5px;align-items:center}
  .skip{position:absolute;top:22px;right:11px;font-family:"Noto Serif",serif;font-size:5.4px;color:var(--ink)}
  .illustration{position:absolute;left:12px;right:12px;top:44px;height:88px;border-radius:42% 48% 45% 40%;
    background:radial-gradient(circle at 50% 50%,var(--teal) 0 48%,var(--teal-soft) 70%,var(--card) 100%)}
  .step-title{position:absolute;left:6px;right:6px;top:143px;text-align:center;
    font-family:"Noto Serif",serif;font-size:8.8px;line-height:10.8px;color:var(--ink)}
  .step-text{position:absolute;left:9px;right:9px;top:168px;text-align:center;
    font-family:"Inter",sans-serif;font-size:4.1px;line-height:6.5px;color:var(--muted)}
  .progress{position:absolute;top:190px;left:50%;transform:translateX(-50%);display:flex;gap:1.3px}
  .progress span{display:block;width:3.6px;height:1.1px;background:var(--dash)}
  .progress span.is-active{width:5.6px;background:var(--teal)}
  .next-button{position:absolute;left:6.5px;right:6.5px;top:201px;height:12.5px;border-radius:1.2px;background:var(--button);
    color:var(--white);font-family:"Inter",sans-serif;font-size:4.3px;font-weight:500;display:flex;align-items:center;justify-content:center}
  .home-indicator{position:absolute;left:50%;top:224px;width:36px;height:1.3px;margin-left:-18px;border-radius:1px;background:var(--home)}
  .screen--first .progress{top:192px}
  .screen--first .next-button{top:205px}
</style>
</head>
<body>
<main class="board">
  <h1 class="board-title">Onboarding</h1>

  <section class="screens">
    <article class="screen screen--splash">
      <span class="brand-name">PLENKO</span>
    </article>

    <article class="screen screen--first">
      <div class="status-bar"><span>9:41</span><span class="status-icons"><svg width="6" height="4" viewBox="0 0 6 4"><rect x="0" y="3" width="1" height="1" fill="#2b2b2b"/><rect x="1.6" y="2" width="1" height="2" fill="#2b2b2b"/><rect x="3.2" y="1" width="1" height="3" fill="#2b2b2b"/><rect x="4.8" y="0" width="1" height="4" fill="#2b2b2b"/></svg><svg width="5" height="4" viewBox="0 0 5 4"><path d="M0 1.4a3.6 3.6 0 0 1 5 0L2.5 4z" fill="#2b2b2b"/></svg><svg width="7" height="4" viewBox="0 0 7 4"><rect x="0" y="0" width="6" height="4" rx="1" fill="#2b2b2b"/><rect x="6.2" y="1.3" width=".8" height="1.4" fill="#2b2b2b"/></svg></span></div>
      <span class="skip">Skip</span>
      <div class="illustration" role="img" aria-label="Room with two ceiling lamps lighting a window and a hand switching on the light"></div>
      <h2 class="step-title">Step 1: Setting Up the Environment</h2>
      <p class="step-text">Ensure two light sources are used to minimize shadows for accurate scanning.</p>
      <div class="progress"><span class="is-active"></span><span></span><span></span><span></span><span></span><span></span><span></span></div>
      <div class="next-button">Next</div>
      <div class="home-indicator"></div>
    </article>

    <article class="screen">
      <div class="status-bar"><span>9:41</span><span class="status-icons"><svg width="6" height="4" viewBox="0 0 6 4"><rect x="0" y="3" width="1" height="1" fill="#2b2b2b"/><rect x="1.6" y="2" width="1" height="2" fill="#2b2b2b"/><rect x="3.2" y="1" width="1" height="3" fill="#2b2b2b"/><rect x="4.8" y="0" width="1" height="4" fill="#2b2b2b"/></svg><svg width="5" height="4" viewBox="0 0 5 4"><path d="M0 1.4a3.6 3.6 0 0 1 5 0L2.5 4z" fill="#2b2b2b"/></svg><svg width="7" height="4" viewBox="0 0 7 4"><rect x="0" y="0" width="6" height="4" rx="1" fill="#2b2b2b"/><rect x="6.2" y="1.3" width=".8" height="1.4" fill="#2b2b2b"/></svg></span></div>
      <span class="skip">Skip</span>
      <div class="illustration" role="img" aria-label="Person removing shoes and rolling up trousers"></div>
      <h2 class="step-title">Step 2: Prepare Your Feet</h2>
      <p class="step-text">Remove shoes and roll up pants for full foot visibility.</p>
      <div class="progress"><span></span><span class="is-active"></span><span></span><span></span><span></span><span></span><span></span></div>
      <div class="next-button">Next</div>
      <div class="home-indicator"></div>
    </article>

    <article class="screen">
      <div class="status-bar"><span>9:41</span><span class="status-icons"><svg width="6" height="4" viewBox="0 0 6 4"><rect x="0" y="3" width="1" height="1" fill="#2b2b2b"/><rect x="1.6" y="2" width="1" height="2" fill="#2b2b2b"/><rect x="3.2" y="1" width="1" height="3" fill="#2b2b2b"/><rect x="4.8" y="0" width="1" height="4" fill="#2b2b2b"/></svg><svg width="5" height="4" viewBox="0 0 5 4"><path d="M0 1.4a3.6 3.6 0 0 1 5 0L2.5 4z" fill="#2b2b2b"/></svg><svg width="7" height="4" viewBox="0 0 7 4"><rect x="0" y="0" width="6" height="4" rx="1" fill="#2b2b2b"/><rect x="6.2" y="1.3" width=".8" height="1.4" fill="#2b2b2b"/></svg></span></div>
      <span class="skip">Skip</span>
      <div class="illustration" role="img" aria-label="Hand holding a phone with the screen facing forward"></div>
      <h2 class="step-title">Step 3: Flip Your Phone</h2>
      <p class="step-text">Turn your device to activate the front-facing sensors for precise depth scanning.</p>
      <div class="progress"><span></span><span></span><span class="is-active"></span><span></span><span></span><span></span><span></span></div>
      <div class="next-button">Next</div>
      <div class="home-indicator"></div>
    </article>

    <article class="screen">
      <div class="status-bar"><span>9:41</span><span class="status-icons"><svg width="6" height="4" viewBox="0 0 6 4"><rect x="0" y="3" width="1" height="1" fill="#2b2b2b"/><rect x="1.6" y="2" width="1" height="2" fill="#2b2b2b"/><rect x="3.2" y="1" width="1" height="3" fill="#2b2b2b"/><rect x="4.8" y="0" width="1" height="4" fill="#2b2b2b"/></svg><svg width="5" height="4" viewBox="0 0 5 4"><path d="M0 1.4a3.6 3.6 0 0 1 5 0L2.5 4z" fill="#2b2b2b"/></svg><svg width="7" height="4" viewBox="0 0 7 4"><rect x="0" y="0" width="6" height="4" rx="1" fill="#2b2b2b"/><rect x="6.2" y="1.3" width=".8" height="1.4" fill="#2b2b2b"/></svg></span></div>
      <span class="skip">Skip</span>
      <div class="illustration" role="img" aria-label="Top view of legs with hands holding a phone 40 cm in front of the foot"></div>
      <h2 class="step-title">Step 4: Positioning Your Phone</h2>
      <p class="step-text">Hold your phone 40 cm away and keep it steady.</p>
      <div class="progress"><span></span><span></span><span></span><span class="is-active"></span><span></span><span></span><span></span></div>
      <div class="next-button">Next</div>
      <div class="home-indicator"></div>
    </article>

    <article class="screen">
      <div class="status-bar"><span>9:41</span><span class="status-icons"><svg width="6" height="4" viewBox="0 0 6 4"><rect x="0" y="3" width="1" height="1" fill="#2b2b2b"/><rect x="1.6" y="2" width="1" height="2" fill="#2b2b2b"/><rect x="3.2" y="1" width="1" height="3" fill="#2b2b2b"/><rect x="4.8" y="0" width="1" height="4" fill="#2b2b2b"/></svg><svg width="5" height="4" viewBox="0 0 5 4"><path d="M0 1.4a3.6 3.6 0 0 1 5 0L2.5 4z" fill="#2b2b2b"/></svg><svg width="7" height="4" viewBox="0 0 7 4"><rect x="0" y="0" width="6" height="4" rx="1" fill="#2b2b2b"/><rect x="6.2" y="1.3" width=".8" height="1.4" fill="#2b2b2b"/></svg></span></div>
      <span class="skip">Skip</span>
      <div class="illustration" role="img" aria-label="Top view of hands moving a phone around the foot while scanning"></div>
      <h2 class="step-title">Step 5: Scanning Your Foot</h2>
      <p class="step-text">Slowly move your upper body around your foot while keeping your elbow steady.</p>
      <div class="progress"><span></span><span></span><span></span><span></span><span class="is-active"></span><span></span><span></span></div>
      <div class="next-button">Next</div>
      <div class="home-indicator"></div>
    </article>

    <article class="screen">
      <div class="status-bar"><span>9:41</span><span class="status-icons"><svg width="6" height="4" viewBox="0 0 6 4"><rect x="0" y="3" width="1" height="1" fill="#2b2b2b"/><rect x="1.6" y="2" width="1" height="2" fill="#2b2b2b"/><rect x="3.2" y="1" width="1" height="3" fill="#2b2b2b"/><rect x="4.8" y="0" width="1" height="4" fill="#2b2b2b"/></svg><svg width="5" height="4" viewBox="0 0 5 4"><path d="M0 1.4a3.6 3.6 0 0 1 5 0L2.5 4z" fill="#2b2b2b"/></svg><svg width="7" height="4" viewBox="0 0 7 4"><rect x="0" y="0" width="6" height="4" rx="1" fill="#2b2b2b"/><rect x="6.2" y="1.3" width=".8" height="1.4" fill="#2b2b2b"/></svg></span></div>
      <span class="skip">Skip</span>
      <div class="illustration" role="img" aria-label="Bare foot with a curved arrow showing a full turn around it"></div>
      <h2 class="step-title">Step 6: Completing the Scan</h2>
      <p class="step-text">Maintain a consistent distance and capture all angles.</p>
      <div class="progress"><span></span><span></span><span></span><span></span><span></span><span class="is-active"></span><span></span></div>
      <div class="next-button">Next</div>
      <div class="home-indicator"></div>
    </article>

    <article class="screen">
      <div class="status-bar"><span>9:41</span><span class="status-icons"><svg width="6" height="4" viewBox="0 0 6 4"><rect x="0" y="3" width="1" height="1" fill="#2b2b2b"/><rect x="1.6" y="2" width="1" height="2" fill="#2b2b2b"/><rect x="3.2" y="1" width="1" height="3" fill="#2b2b2b"/><rect x="4.8" y="0" width="1" height="4" fill="#2b2b2b"/></svg><svg width="5" height="4" viewBox="0 0 5 4"><path d="M0 1.4a3.6 3.6 0 0 1 5 0L2.5 4z" fill="#2b2b2b"/></svg><svg width="7" height="4" viewBox="0 0 7 4"><rect x="0" y="0" width="6" height="4" rx="1" fill="#2b2b2b"/><rect x="6.2" y="1.3" width=".8" height="1.4" fill="#2b2b2b"/></svg></span></div>
      <span class="skip">Skip</span>
      <div class="illustration" role="img" aria-label="Two bare feet side by side"></div>
      <h2 class="step-title">Step 7: Repeat for the Other Foot</h2>
      <p class="step-text">Follow the same scanning process to ensure accurate data for both feet.</p>
      <div class="progress"><span></span><span></span><span></span><span></span><span></span><span></span><span class="is-active"></span></div>
      <div class="next-button">Next</div>
      <div class="home-indicator"></div>
    </article>
  </section>
</main>
</body>
</html>
```